RW Framewell Inc Business cards

We need business cards using our existing logo but slightly modified. Right now the logo says RW Framewell. We want to keep the RW part of the design, but replace the FRAMEWELL portion with "FRAMEWELL". Please see the attached file.
Ideally this would be a blank template so we can add Different Names, titles, and phone numbers later.
On the one side we want only the logo and on the other side the detail. I'm attaching an example for you to see.
Please reach out with any other questions. Our address and other details will be given out once we find a design we like.

Target Market(s)

Construction Industry

```html
<!DOCTYPE html>
<html lang="en">
<head>
<meta charset="utf-8">
<title>RW Framewell Inc Business Cards</title>
<link rel="stylesheet" href="https://fonts.googleapis.com/css2?family=Oswald:wght@500&family=Roboto:wght@400&family=Roboto+Condensed:wght@400&display=swap">
<style>
  :root {
    --backdrop: #dde9f2;
    --card-white: #ffffff;
    --brand-blue: #1f77bd;
    --ink: #222222;
    --silver: #d3d6d9;
  }
  html, body {
    margin: 0;
    padding: 0;
    width: 1200px;
    height: 1200px;
    overflow: hidden;
    background: var(--backdrop);
  }
  .canvas {
    position: relative;
    width: 1200px;
    height: 1200px;
  }
  .card {
    position: absolute;
    left: 283px;
    width: 634px;
    height: 362px;
  }
  .card--front { top: 174px; background: var(--card-white); }
  .card--back { top: 609px; background: var(--brand-blue); }

  .brand {
    position: absolute;
    display: flex;
    align-items: center;
    gap: 12px;
    font-family: "Roboto Condensed", "Arial Narrow", sans-serif;
    font-weight: 400;
  }
  .brand__square { flex: none; }
  .brand__name { display: flex; flex-direction: column; line-height: 1; }
  .brand__initials { letter-spacing: 2px; }
  .brand__words { text-transform: uppercase; }

  .card--front .brand { left: 60px; top: 126px; color: var(--brand-blue); }
  .card--front .brand__square { width: 18px; height: 18px; background: var(--brand-blue); }
  .card--front .brand__initials { font-size: 64px; }
  .card--front .brand__words { font-size: 16px; margin-top: 8px; letter-spacing: 7px; }

  .card--back .brand { left: 50%; top: 50%; transform: translate(-50%, -50%); color: var(--silver); }
  .card--back .brand__square { width: 26px; height: 26px; background: var(--silver); }
  .card--back .brand__initials { font-size: 96px; }
  .card--back .brand__words { font-size: 24px; margin-top: 10px; letter-spacing: 10px; }

  .divider {
    position: absolute;
    left: 317px;
    top: 91px;
    width: 1px;
    height: 180px;
    background: var(--brand-blue);
  }
  .details {
    position: absolute;
    left: 350px;
    top: 96px;
    font-family: "Roboto", Arial, sans-serif;
    color: var(--ink);
  }
  .details__name {
    margin: 0;
    font-family: "Oswald", "Arial Narrow", sans-serif;
    font-weight: 500;
    font-size: 26px;
    line-height: 30px;
    color: var(--brand-blue);
    text-transform: uppercase;
    letter-spacing: -0.3px;
  }
  .details__title { margin: 0; font-size: 16px; line-height: 20px; }
  .details__address { margin: 17px 0 0; font-size: 16px; line-height: 21px; font-style: normal; }
  .contact { list-style: none; margin: 10px 0 0; padding: 0; }
  .contact__item {
    display: flex;
    align-items: center;
    gap: 8px;
    font-size: 16px;
    line-height: 20.5px;
  }
  .contact__icon { width: 13px; height: 13px; flex: none; }
</style>
</head>
<body>
<div class="canvas">
  <section class="card card--front" aria-label="Business card, details side">
    <div class="brand">
      <span class="brand__square" aria-hidden="true"></span>
      <span class="brand__name">
        <span class="brand__initials">RW</span>
        <span class="brand__words">Framewell</span>
      </span>
    </div>
    <div class="divider" aria-hidden="true"></div>
    <div class="details">
      <h1 class="details__name">Rowan Whitlock</h1>
      <p class="details__title">Owner</p>
      <address class="details__address">418 Ridgeline Avenue Kelston,<br>BC Canada V0X 2L7</address>
      <ul class="contact">
        <li class="contact__item">
          <svg class="contact__icon" viewBox="0 0 16 16" aria-hidden="true"><path fill="#1f77bd" d="M3.5 1.5l2.4-.4 1.3 3.4-1.6 1.2c.7 1.7 1.9 3 3.6 3.8l1.3-1.5 3.3 1.4-.4 2.5c-.2.8-.9 1.3-1.7 1.2C6.6 12.6 2.6 8.6 2.3 3.2c0-.8.4-1.5 1.2-1.7z"/></svg>
          <span>+1 555 014 2890</span>
        </li>
        <li class="contact__item">
          <svg class="contact__icon" viewBox="0 0 16 16" aria-hidden="true"><rect x="1" y="4" width="14" height="10" rx="1" fill="none" stroke="#1f77bd" stroke-width="1.6"/><path d="M1.5 4.8L8 9.5l6.5-4.7" fill="none" stroke="#1f77bd" stroke-width="1.6"/></svg>
          <span>rwhitlock@rwframewell.com</span>
        </li>
        <li class="contact__item">
          <svg class="contact__icon" viewBox="0 0 16 16" aria-hidden="true"><g fill="none" stroke="#1f77bd" stroke-width="1.3"><circle cx="8" cy="8" r="6.5"/><ellipse cx="8" cy="8" rx="3" ry="6.5"/><path d="M1.5 8h13M2.5 4.8h11M2.5 11.2h11"/></g></svg>
          <span>www.rwframewell.com</span>
        </li>
      </ul>
    </div>
  </section>

  <section class="card card--back" aria-label="Business card, logo side">
    <div class="brand">
      <span class="brand__square" aria-hidden="true"></span>
      <span class="brand__name">
        <span class="brand__initials">RW</span>
        <span class="brand__words">Framewell</span>
      </span>
    </div>
  </section>
</div>
</body>
</html>
```